Business Card Design for Training Business

Clear Path Coaching is a new business that delivers training and other services with a focus on topics related to mental health and wellbeing, for example, Wellmind Response Course, Resilience etc. We have a strong focus on evidence-based psychology and neuroscience. I have a logo which I will upload with the brief, so please consider colours that work well with the logo.
Target Market(s)
Adults, workplaces (particularly government and not-for-profits)
Industry/Entity Type
Business
Contact Information for Business Card
Head Strong TrainingSamantha SellwoodDirector0438 770 850sam@headstrongtraining.com.auwww.headstrongtraining.com.au

```html
<!DOCTYPE html>
<html lang="en">
<head>
<meta charset="utf-8">
<title>Clear Path Coaching – Business Card</title>
<link rel="stylesheet" href="https://fonts.googleapis.com/css2?family=Didact+Gothic&display=swap">
<style>
  :root {
    --backdrop: #e9e9e9;
    --card: #ffffff;
    --teal: #12b1ab;
    --ink: #1f1f1f;
    --muted: #8a8a8a;
  }
  html, body {
    margin: 0;
    width: 1200px;
    height: 898px;
    overflow: hidden;
    background: var(--backdrop);
    font-family: "Didact Gothic", sans-serif;
  }
  .card {
    position: absolute;
    left: 180px;
    top: 209px;
    width: 840px;
    height: 480px;
    background: var(--card);
    overflow: hidden;
    box-shadow: 0 6px 24px rgba(0,0,0,0.15);
  }
  .card__band {
    position: absolute;
    inset: 0;
  }
  .brand {
    position: absolute;
    left: 70px;
    top: 150px;
    width: 290px;
    text-align: center;
  }
  .brand__mark {
    display: block;
    width: 104px;
    height: 104px;
    margin: 0 auto 14px;
    border-radius: 50%;
    background: var(--teal);
  }
  .brand__name {
    margin: 0;
    font-size: 25px;
    letter-spacing: 3px;
    color: var(--muted);
    font-weight: 400;
  }
  .person {
    position: absolute;
    left: 82px;
    top: 338px;
  }
  .person__name {
    margin: 0;
    font-size: 38px;
    font-weight: 400;
    color: var(--ink);
  }
  .person__role {
    margin: 2px 0 0 2px;
    font-size: 19px;
    letter-spacing: 1px;
    color: var(--ink);
  }
  .contact {
    position: absolute;
    left: 478px;
    top: 142px;
    margin: 0;
    padding: 0;
    list-style: none;
    font-size: 17px;
    line-height: 30px;
    color: var(--ink);
  }
</style>
</head>
<body>
  <section class="card">
    <svg class="card__band" width="840" height="480" viewBox="0 0 840 480" aria-hidden="true">
      <path d="M300 -20 L418 130 L418 272 L590 500" fill="none" stroke="var(--teal)" stroke-width="38" stroke-linejoin="round"/>
      <g fill="none" stroke="#fff" stroke-width="2" stroke-linecap="round" stroke-linejoin="round">
        <path d="M412 160 q0 -6 3 -6 l2 3 -2 2 q2 5 6 7 l2 -2 3 2 q0 4 -6 3 q-8 -3 -8 -9z" fill="#fff" stroke="none"/>
        <rect x="409" y="187" width="18" height="12" rx="1"/>
        <path d="M409 188 l9 6 9 -6"/>
        <circle cx="418" cy="227" r="8"/>
        <path d="M410 227 h16 M418 219 q-5 8 0 16 M418 219 q5 8 0 16"/>
      </g>
    </svg>

    <div class="brand">
      <span class="brand__mark"></span>
      <p class="brand__name">CLEAR PATH COACHING</p>
    </div>

    <div class="person">
      <h1 class="person__name">Rebecca Tanfield</h1>
      <p class="person__role">DIRECTOR</p>
    </div>

    <ul class="contact">
      <li>0491 362 517</li>
      <li>bec@clearpathcoaching.example.au</li>
      <li>www.clearpathcoaching.example.au</li>
    </ul>
  </section>
</body>
</html>
```